Valmora Company needs a Business Card Design

We just opened our business recently and we need a business card design. Our basic product are clothes and accessories. We would like to see designs that use bright colors like pink, light blue and purple. In addition to that kindly include also our address in the business card which our main office is located in Los Angeles, California.
The final design should communicate that we have affordable price yet high quality brand.

Target Market(s)

young and middle age women

Industry/Entity Type

Business

Contact Information for Business Card

Valmora Apparel and Accessories 4873 North Bellcrest St. Los Angeles California
Tel: 555-318-6492

Logo Text

Valmora's Apparel and Accessories

Font styles to use
Serif

Requirements
Must have
• there should be a graphic of a sexy lady wearing an elegant dress at the upper left corner of the business card.

```html
<!DOCTYPE html>
<html lang="en">
<head>
<meta charset="utf-8">
<title>Valmora Apparel and Accessories – Business Card</title>
<link rel="stylesheet" href="https://fonts.googleapis.com/css2?family=Andika&family=Arimo:wght@700&display=swap">
<style>
  :root {
    --plum-deep: #4a0a30;
    --plum: #7a0d4d;
    --magenta: #b80f72;
    --magenta-bright: #d4147f;
    --blush: #f2a9bb;
    --blush-soft: #f6c3c9;
    --lilac-text: #9a68b1;
    --white: #ffffff;
    --model-dark: #1c2448;
    --model-mid: #3d4f8f;
    --model-skin: #d9a88f;
  }
  html, body {
    margin: 0;
    padding: 0;
    width: 1200px;
    height: 722px;
    overflow: hidden;
    background: #ffffff;
  }
  .card {
    position: relative;
    width: 1200px;
    height: 722px;
    overflow: hidden;
    background:
      radial-gradient(ellipse 520px 380px at 1120px 640px, var(--blush-soft) 0%, var(--blush) 35%, rgba(242,169,187,0) 75%),
      radial-gradient(ellipse 600px 420px at 560px 560px, var(--magenta-bright) 0%, rgba(212,20,127,0) 70%),
      radial-gradient(ellipse 500px 360px at 700px 300px, var(--magenta) 0%, rgba(184,15,114,0) 75%),
      linear-gradient(160deg, var(--plum) 0%, var(--plum-deep) 45%, var(--plum) 100%);
  }
  .model-photo {
    position: absolute;
    left: 72px;
    top: 40px;
    width: 90px;
    height: 324px;
  }
  .contact {
    position: absolute;
    right: 635px;
    top: 0;
    font-family: "Andika", sans-serif;
    color: var(--white);
    font-size: 30px;
    text-align: right;
    letter-spacing: 0.5px;
  }
  .contact p {
    position: absolute;
    right: 0;
    margin: 0;
    white-space: nowrap;
    line-height: 1;
  }
  .contact .street { top: 290px; }
  .contact .city { top: 332px; }
  .contact .phone { top: 417px; }
  .divider {
    position: absolute;
    left: 604px;
    top: 195px;
    width: 2px;
    height: 315px;
    background: var(--white);
  }
  .brand {
    position: absolute;
    left: 636px;
    top: 0;
    font-family: "Arimo", sans-serif;
    font-weight: 700;
    color: var(--lilac-text);
    margin: 0;
  }
  .brand span {
    position: absolute;
    left: 0;
    white-space: nowrap;
    line-height: 1;
  }
  .brand .name { top: 218px; font-size: 62px; }
  .brand .line-1 { top: 280px; font-size: 70px; }
  .brand .line-2 { top: 353px; font-size: 70px; }
  .brand .line-3 { top: 433px; font-size: 70px; }
</style>
</head>
<body>
  <main class="card">
    <svg class="model-photo" role="img" aria-label="Photo of a woman in an elegant short starry dress and ankle boots" viewBox="0 0 90 324">
      <defs>
        <linearGradient id="modelTone" x1="0" y1="0" x2="0" y2="1">
          <stop offset="0" stop-color="#5a3a32"/>
          <stop offset="0.2" stop-color="var(--model-mid)"/>
          <stop offset="0.5" stop-color="var(--model-dark)"/>
          <stop offset="0.6" stop-color="var(--model-skin)"/>
          <stop offset="0.88" stop-color="var(--model-skin)"/>
          <stop offset="1" stop-color="#1a1a1a"/>
        </linearGradient>
      </defs>
      <rect x="0" y="0" width="90" height="324" rx="20" fill="url(#modelTone)" opacity="0.85"/>
    </svg>

    <section class="contact">
      <p class="street">4873 North Bellcrest St.</p>
      <p class="city">Los Angeles California</p>
      <p class="phone">Tel: 555-318-6492</p>
    </section>

    <div class="divider"></div>

    <h1 class="brand">
      <span class="name">Valmora</span>
      <span class="line-1">Apparel</span>
      <span class="line-2">and</span>
      <span class="line-3">Accessories</span>
    </h1>
  </main>
</body>
</html>
```